CD Cover Design Project w/ Committed Payout.

We need a CD cover design for our first release from our new christian record label.

The title of the CD is called

"The Bright Harbor Sessions Volume 1"

This will have to tactfully go on the cover...

Perhaps the attached logo can be somewhere on the cover and "presents" and then the CD name...

Additionally - will need the back of the CD as well to co-inside with the front design. The back design will have artist and song listing as well as the 372 Records logo on the bottom, and the CD # which will be #372-1 with a place for a UPC scanner code.

Please leave the artist and song lists as "Artist 1 - Song 1", etc. for now

Target Market(s)

everyone

Industry/Entity Type

Christian

Requirements
Must have
• something with the image of the world and somehow something positively impacting it.

```html
<!DOCTYPE html>
<html lang="en">
<head>
<meta charset="utf-8">
<title>The Bright Harbor Sessions Volume 1 – CD Cover</title>
<link rel="stylesheet" href="https://fonts.googleapis.com/css2?family=PT+Sans:wght@400;700&family=Yeseva+One&display=swap">
<style>
  :root {
    --cover-magenta: #a5336f;
    --cover-magenta-deep: #8f2862;
    --silhouette-plum: #6a1c48;
    --globe-blue: #5d6fb8;
    --globe-glow: #f6d98a;
    --spine-violet: #9b3b8f;
    --spine-edge: #b45aa4;
    --label-black: #0c0c0c;
    --text-white: #ffffff;
    --text-soft: #f3dbe8;
    --title-gold: #f1c54a;
    --title-amber: #c7902b;
  }
  html, body {
    margin: 0;
    padding: 0;
    width: 1200px;
    height: 585px;
    overflow: hidden;
    background: var(--cover-magenta);
  }
  .cd-spread {
    position: relative;
    width: 1200px;
    height: 585px;
    overflow: hidden;
    background: var(--cover-magenta);
    font-family: "PT Sans", Arial, sans-serif;
    color: var(--text-white);
  }

  /* Panels */
  .back-panel, .front-panel {
    position: absolute;
    top: 0;
    height: 585px;
    background: radial-gradient(ellipse at 50% 40%, var(--cover-magenta) 0%, var(--cover-magenta-deep) 100%);
  }
  .back-panel { left: 0; width: 585px; }
  .front-panel { left: 615px; width: 585px; }

  /* Illustration areas */
  .back-artwork {
    position: absolute;
    left: 0;
    top: 60px;
    width: 335px;
    height: 525px;
    background: radial-gradient(ellipse at 40% 58%, var(--silhouette-plum) 0%, var(--silhouette-plum) 50%, rgba(106,28,72,0) 75%);
  }
  .front-artwork {
    position: absolute;
    left: 20px;
    top: 10px;
    width: 520px;
    height: 440px;
    background: radial-gradient(ellipse at 62% 45%, rgba(106,28,72,0.95) 0%, rgba(106,28,72,0.6) 32%, rgba(106,28,72,0) 68%);
  }
  .world-artwork {
    position: absolute;
    left: 410px;
    top: 175px;
    width: 110px;
    height: 110px;
    border-radius: 50%;
    background: radial-gradient(circle at 35% 30%, var(--globe-glow) 0%, var(--globe-blue) 45%, rgba(93,111,184,0.2) 100%);
    opacity: 0.55;
  }

  /* Label mark */
  .label-mark {
    position: absolute;
    display: flex;
    align-items: center;
    gap: 7px;
    font-weight: 700;
    font-size: 16px;
    color: var(--text-white);
    white-space: nowrap;
  }
  .label-mark__square {
    width: 18px;
    height: 18px;
    background: var(--label-black);
  }
  .back-panel .label-mark { left: 368px; top: 438px; }
  .front-panel .label-mark { right: 30px; top: 50px; }

  .presents {
    position: absolute;
    right: 42px;
    top: 104px;
    margin: 0;
    font-size: 14px;
    letter-spacing: 0.5px;
    text-transform: uppercase;
  }

  /* Back cover info */
  .track-list {
    position: absolute;
    left: 368px;
    top: 70px;
    margin: 0;
    padding: 0;
    list-style: none;
    font-size: 14px;
    line-height: 1.95;
    color: var(--text-soft);
  }
  .catalog-number {
    position: absolute;
    left: 368px;
    top: 470px;
    margin: 0;
    font-size: 14px;
    font-weight: 700;
  }
  .upc-area {
    position: absolute;
    left: 460px;
    top: 505px;
    width: 100px;
    height: 55px;
    background: var(--text-white);
  }

  /* Spine */
  .spine {
    position: absolute;
    left: 585px;
    top: 0;
    width: 30px;
    height: 585px;
    background: var(--spine-violet);
    border-left: 1px solid var(--spine-edge);
    border-right: 1px solid var(--spine-edge);
    box-sizing: border-box;
  }
  .spine__title {
    position: absolute;
    left: 50%;
    top: 140px;
    transform-origin: 0 0;
    transform: rotate(90deg) translateY(-50%);
    font-weight: 700;
    font-size: 14px;
    letter-spacing: 1.6px;
    white-space: nowrap;
  }

  /* Front title */
  .album-title {
    position: absolute;
    left: 60px;
    top: 300px;
    width: 460px;
    margin: 0;
    font-weight: normal;
  }
  .album-title__the,
  .album-title__main {
    display: block;
    font-family: "Yeseva One", Georgia, serif;
    color: var(--text-white);
    text-shadow: 3px 3px 0 var(--title-gold), 5px 5px 0 var(--title-amber);
  }
  .album-title__the {
    font-size: 58px;
    line-height: 1;
    margin-left: 100px;
  }
  .album-title__main {
    font-size: 50px;
    line-height: 1.2;
    white-space: nowrap;
  }
  .album-title__sub {
    display: block;
    font-family: "Yeseva One", Georgia, serif;
    font-size: 30px;
    line-height: 1.1;
    text-align: right;
    margin-right: -3px;
    color: var(--text-white);
    text-shadow: 2px 2px 0 var(--title-gold);
  }
  .album-title__volume {
    display: block;
    font-weight: 700;
    font-size: 22px;
    text-align: right;
    margin-right: 8px;
    margin-top: 2px;
  }
</style>
</head>
<body>
<main class="cd-spread">

  <section class="back-panel" aria-label="Back cover">
    <div class="back-artwork" role="img" aria-label="Silhouette of a head in profile with music notes rising from the hair"></div>
    <ol class="track-list">
      <li>Artist 1 - Song 1</li>
      <li>Artist 2 - Song 2</li>
      <li>Artist 3 - Song 3</li>
      <li>Artist 4 - Song 4</li>
      <li>Artist 5 - Song 5</li>
      <li>Artist 6 - Song 6</li>
      <li>Artist 7 - Song 7</li>
      <li>Artist 8 - Song 8</li>
      <li>Artist 9 - Song 9</li>
      <li>Artist 10 - Song 10</li>
    </ol>
    <div class="label-mark">
      <span class="label-mark__square"></span>
      <span class="label-mark__name">372 Records</span>
    </div>
    <p class="catalog-number">#372-1</p>
    <div class="upc-area" role="img" aria-label="Space reserved for the UPC code"></div>
  </section>

  <section class="spine" aria-label="Spine">
    <span class="spine__title">The Bright Harbor Sessions Volume 1</span>
  </section>

  <section class="front-panel" aria-label="Front cover">
    <div class="front-artwork" role="img" aria-label="Silhouette of a head in profile with music notes, a treble clef and staff lines swirling around it"></div>
    <div class="world-artwork" role="img" aria-label="The world glowing with light carried by the music"></div>
    <div class="label-mark">
      <span class="label-mark__square"></span>
      <span class="label-mark__name">372 Records</span>
    </div>
    <p class="presents">Presents</p>
    <h1 class="album-title">
      <span class="album-title__the">The</span>
      <span class="album-title__main">Bright Harbor</span>
      <span class="album-title__sub">Sessions</span>
      <span class="album-title__volume">Volume 1</span>
    </h1>
  </section>

</main>
</body>
</html>
```